Brindovalle Business cards

Dear team, I need to get the design file to suit it to our team. The focus of the business card is the Automotive Market and the design must be in black colour and the logo must be in glossy black. On the front of the card I need to get the following info:

- Name and Surname
- Title
- eMail
- Phone Number
- Skype account
- domain address

```html
<!DOCTYPE html>
<html lang="en">
<head>
<meta charset="utf-8">
<title>Brindovalle Business Cards</title>
<link href="https://fonts.googleapis.com/css2?family=Poppins:wght@600;700&family=Roboto:wght@400;500&display=swap" rel="stylesheet">
<style>
  :root {
    --bg: #d9d9dc;
    --card: #1c1c1e;
    --card-deep: #0e0e0f;
    --red: #e8232f;
    --white: #ffffff;
    --muted: #e6e6e6;
  }
  html, body {
    margin: 0;
    width: 1200px;
    height: 912px;
    overflow: hidden;
    background: var(--bg);
  }
  .canvas { position: relative; width: 1200px; height: 912px; }
  .card {
    position: absolute;
    width: 620px;
    height: 354px;
    border-radius: 4px;
    overflow: hidden;
    box-shadow: 0 10px 28px rgba(0,0,0,.25);
  }
  .card-back { left: 70px; top: 60px; }
  .pattern-fill {
    position: absolute; inset: 0;
    background: linear-gradient(135deg, var(--card-deep) 0%, #232325 45%, #3a3a3d 75%, #1a1a1b 100%);
  }
  .card-front {
    left: 510px; top: 488px;
    background: var(--card);
    font-family: "Roboto", Arial, sans-serif;
    color: var(--white);
  }
  .brand {
    position: absolute; right: 40px; top: 44px;
    display: flex; align-items: center; gap: 12px;
  }
  .brand-square { width: 34px; height: 34px; background: var(--red); }
  .brand-name {
    font-family: "Poppins", Arial, sans-serif;
    font-weight: 700; font-size: 38px; line-height: 1;
    color: var(--white); letter-spacing: -.5px;
  }
  .divider-long {
    position: absolute; left: 150px; right: 40px; top: 118px;
    height: 2px; background: var(--red);
  }
  .address {
    position: absolute; right: 40px; top: 134px;
    text-align: right; font-size: 16px; line-height: 1.3; color: var(--muted);
  }
  .person { position: absolute; left: 40px; top: 150px; }
  .person-name {
    font-family: "Poppins", Arial, sans-serif;
    font-weight: 700; font-size: 30px; line-height: 1;
    color: var(--red); letter-spacing: .5px; text-transform: uppercase;
  }
  .person-title { font-size: 17px; margin-top: 4px; }
  .divider-short {
    position: absolute; left: 40px; top: 222px;
    width: 230px; height: 2px; background: var(--red);
  }
  .contacts {
    position: absolute; left: 40px; top: 232px;
    margin: 0; padding: 0; list-style: none;
    font-size: 17px; line-height: 25px;
  }
  .contacts li { display: flex; align-items: center; gap: 8px; }
  .contacts svg { width: 14px; height: 14px; flex: none; }
  .swoosh { position: absolute; left: 0; bottom: 0; }
</style>
</head>
<body>
<main class="canvas">
  <section class="card card-back">
    <div class="pattern-fill" role="img" aria-label="Glossy black repeating brand pattern with one red accent tile"></div>
  </section>

  <section class="card card-front">
    <div class="brand">
      <span class="brand-square"></span>
      <span class="brand-name">Brindovalle</span>
    </div>
    <div class="divider-long"></div>
    <p class="address" style="margin:0">2140 W Harlan Ave, Fairmont,<br>Ohio 44020</p>

    <div class="person">
      <div class="person-name">Marlo Venn</div>
      <div class="person-title">Director</div>
    </div>
    <div class="divider-short"></div>

    <ul class="contacts">
      <li>
        <svg viewBox="0 0 24 24"><path fill="#e8232f" d="M6.6 10.8a15.1 15.1 0 0 0 6.6 6.6l2.2-2.2c.3-.3.7-.4 1-.2 1.1.4 2.3.6 3.6.6.6 0 1 .4 1 1V20c0 .6-.4 1-1 1A17 17 0 0 1 3 4c0-.6.4-1 1-1h3.5c.6 0 1 .4 1 1 0 1.3.2 2.5.6 3.6.1.3 0 .7-.2 1z"/></svg>
        555-014-2290
      </li>
      <li>
        <svg viewBox="0 0 24 24"><rect x="2" y="5" width="20" height="14" fill="#e8232f"/><path d="M2 5l10 8 10-8" fill="none" stroke="#1c1c1e" stroke-width="2"/></svg>
        info@brindovalle.com
      </li>
      <li>
        <svg viewBox="0 0 24 24"><circle cx="12" cy="12" r="10" fill="#e8232f"/></svg>
        brindovalle
      </li>
    </ul>

    <svg class="swoosh" width="620" height="354" viewBox="0 0 620 354">
      <path fill="#ffffff" d="M0,318 L392,290 C405,289 412,284 418,276 L430,258 L436,262 L426,292 C418,304 410,308 396,309 L0,336 Z"/>
      <path fill="#e8232f" d="M620,236 H490 C464,236 452,246 442,262 L430,284 C422,300 412,310 396,312 L0,340 V354 H620 Z"/>
    </svg>
  </section>
</main>
</body>
</html>
```